Business Card Design

Business Card for professional consulting firm working with large financial institutions.

Target Market(s)

Executive buyers

Industry/Entity Type

Banking

Contact Information for Business Card

Mild creativity wanted. Not boring, but do elaborate artwork.

Font styles to use
Serif
Sans Serif

Colors

Designer to choose colors to be used in the design.

Requirements
Must have
• Standard business card features - company name, individual name, telephone, website, email, locations.
Nice to have
• Two colors
Should not have
• too many colors, fancy printing, cartoons.

```html
<!DOCTYPE html>
<html lang="en">
<head>
<meta charset="utf-8">
<title>Northmere – Business Card</title>
<link rel="stylesheet" href="https://fonts.googleapis.com/css2?family=Lora:wght@400&family=Work+Sans:wght@400;600&display=swap">
<style>
  :root {
    --bg: #e9e9ea;
    --card-dark: #3b3b3d;
    --card-light: #ffffff;
    --ink: #2f2f31;
    --ink-soft: #4a4a4c;
    --name-grey: #b9b9bb;
    --swoosh: #c4c4c6;
    --rule: #3a3a3c;
    --logo-on-dark: #ffffff;
    --logo-on-light: #3a3a3c;
  }
  * { margin: 0; padding: 0; box-sizing: border-box; }
  html, body { width: 1200px; height: 930px; overflow: hidden; background: var(--bg); }
  .canvas { position: relative; width: 1200px; height: 930px; }

  .card {
    position: absolute;
    width: 600px;
    height: 343px;
    border-radius: 18px;
    overflow: hidden;
    box-shadow: 0 6px 18px rgba(0,0,0,0.18);
  }
  .card--back { left: 80px; top: 80px; background: var(--card-dark); }
  .card--front { left: 520px; top: 507px; background: var(--card-light); }

  .brand {
    font-family: "Lora", serif;
    font-weight: 400;
    letter-spacing: 0.5px;
  }
  .card--back .brand {
    position: absolute;
    left: 0; right: 0; top: 50%;
    transform: translateY(-50%);
    text-align: center;
    font-size: 46px;
    color: var(--logo-on-dark);
  }
  .card--front .brand {
    position: absolute;
    left: 40px; top: 38px;
    font-size: 30px;
    color: var(--logo-on-light);
  }

  .card-art { position: absolute; inset: 0; width: 600px; height: 343px; }

  .person {
    position: absolute;
    right: 36px; top: 30px;
    text-align: right;
    font-family: "Work Sans", sans-serif;
  }
  .person__name {
    font-size: 25px;
    font-weight: 600;
    color: var(--name-grey);
    letter-spacing: 0.5px;
    text-transform: uppercase;
  }
  .person__role {
    font-size: 13px;
    color: var(--ink);
    margin-top: 1px;
  }

  .address {
    position: absolute;
    right: 36px; top: 148px;
    text-align: right;
    font-family: "Work Sans", sans-serif;
    font-size: 14px;
    line-height: 1.4;
    color: var(--ink);
  }

  .contacts {
    position: absolute;
    left: 30px; top: 208px;
    list-style: none;
    font-family: "Work Sans", sans-serif;
    font-size: 15px;
    line-height: 1.45;
    color: var(--ink);
  }
  .contacts li { display: flex; align-items: center; gap: 8px; }
  .contacts svg { width: 10px; height: 10px; flex: none; }
</style>
</head>
<body>
<main class="canvas">

  <section class="card card--back" aria-label="Card back">
    <p class="brand">northmere</p>
  </section>

  <section class="card card--front" aria-label="Card front">
    <svg class="card-art" viewBox="0 0 600 343" aria-hidden="true">
      <line x1="36" y1="124" x2="564" y2="124" stroke="var(--rule)" stroke-width="1.4"/>
      <path d="M0 343 L0 322 C150 318 400 270 600 160 L600 343 Z" fill="var(--card-dark)"/>
      <path d="M120 313 C300 300 470 250 600 150 L600 176 C480 255 310 300 120 313 Z" fill="var(--swoosh)"/>
    </svg>

    <p class="brand">northmere</p>

    <div class="person">
      <p class="person__name">Daniel Hart</p>
      <p class="person__role">Director</p>
    </div>

    <address class="address">27 Wexford St,<br>Alderton VIC 3712</address>

    <ul class="contacts">
      <li>
        <svg viewBox="0 0 10 10"><path d="M2 1 L4 1 L4.6 3 L3.4 3.8 C4 5.2 4.8 6 6.2 6.6 L7 5.4 L9 6 L9 8 C5 8.5 1.5 5 2 1 Z" fill="var(--ink-soft)"/></svg>
        +330 5170-4412
      </li>
      <li>
        <svg viewBox="0 0 10 10"><rect x="1" y="2.5" width="8" height="5.5" fill="none" stroke="var(--ink-soft)" stroke-width="0.9"/><path d="M1 2.5 L5 5.6 L9 2.5" fill="none" stroke="var(--ink-soft)" stroke-width="0.9"/></svg>
        info@northmere.com
      </li>
      <li>
        <svg viewBox="0 0 10 10"><circle cx="5" cy="5" r="4" fill="none" stroke="var(--ink-soft)" stroke-width="0.9"/><ellipse cx="5" cy="5" rx="1.8" ry="4" fill="none" stroke="var(--ink-soft)" stroke-width="0.7"/><line x1="1" y1="5" x2="9" y2="5" stroke="var(--ink-soft)" stroke-width="0.7"/></svg>
        www.northmere.com
      </li>
    </ul>
  </section>

</main>
</body>
</html>
```